Aerial Imaging and photgraphy business card

Design a business card with eye catching aerial photo of country side / landscape with a drone in the foreground.
Also contact details.

Target Market(s)

Aerial Imaging photography

Industry/Entity Type

Advertising

Contact Information for Business Card

Rowland
0412965203
Website http://www.skywardvistaphoto.com.au/
email address : skywardvistaphoto.com.au

Colors
e8f1ca
cadf82
9bcb3c
33a6d7
85cae6
cee9f5

Requirements
Must have
• High res photo
• Korvane drone in the foreground Either T4200 and korvane Glidewing or both
Nice to have
• high resolution landscape country photo on the front of the card with a Korvane T4200 drone in the foreground.

```html
<!DOCTYPE html>
<html lang="en">
<head>
<meta charset="utf-8">
<title>Skyward Vista Photo — Business Card</title>
<link href="https://fonts.googleapis.com/css2?family=Open+Sans:wght@400;700&display=swap" rel="stylesheet">
<style>
  :root {
    --page-bg: #eeeeee;
    --card-white: #ffffff;
    --accent-red: #a3202b;
    --text-grey: #555555;
    --text-dark: #333333;
    --sky-haze: #e3efe6;
    --mist-teal: #a9cfcb;
    --hill-blue: #6f9fae;
    --hill-deep: #4f7f8c;
    --field-light: #8fc45a;
    --field-green: #5f9a4a;
    --field-deep: #2c5a30;
    --badge-blue: #33a6d7;
  }
  * { margin: 0; padding: 0; box-sizing: border-box; }
  html, body {
    width: 1200px; height: 900px; overflow: hidden;
    background: var(--page-bg);
    font-family: "Open Sans", Arial, sans-serif;
  }
  .card-set {
    position: absolute; inset: 0;
    display: flex; align-items: center; justify-content: center; gap: 40px;
  }
  .card {
    width: 540px; height: 330px;
    background: var(--card-white);
    position: relative;
    box-shadow: 0 4px 14px rgba(0,0,0,0.12);
    overflow: hidden;
  }
  .contact-side .holder {
    position: absolute; left: 44px; top: 40px;
  }
  .holder-name {
    color: var(--accent-red); font-weight: 700; font-size: 19px; line-height: 1.2;
  }
  .holder-title {
    color: var(--text-grey); font-size: 13px; margin-top: 2px;
  }
  .contact-list {
    position: absolute; left: 44px; top: 124px; list-style: none;
  }
  .contact-list li {
    display: flex; align-items: center; gap: 10px;
    color: var(--text-dark); font-size: 13.5px; line-height: 1; margin-bottom: 14px;
    white-space: nowrap;
  }
  .contact-list svg { width: 13px; height: 13px; flex: none; }
  .brand-mark {
    position: absolute; left: 214px; top: 232px;
    display: flex; align-items: center; gap: 12px;
    white-space: nowrap;
  }
  .brand-circle {
    width: 40px; height: 40px; border-radius: 50%;
    background: var(--badge-blue); flex: none;
  }
  .brand-name {
    color: var(--text-dark); font-weight: 700; font-size: 21px; letter-spacing: 0.5px;
    text-transform: uppercase; line-height: 1;
  }
  .photo-side .landscape {
    position: absolute; inset: 0;
    background:
      radial-gradient(ellipse 55% 40% at 30% 95%, rgba(44,90,48,0.85), transparent 70%),
      radial-gradient(ellipse 45% 30% at 15% 55%, rgba(143,196,90,0.55), transparent 70%),
      radial-gradient(ellipse 60% 22% at 75% 48%, rgba(79,127,140,0.75), transparent 70%),
      radial-gradient(ellipse 35% 20% at 55% 45%, rgba(70,75,80,0.35), transparent 70%),
      linear-gradient(160deg,
        var(--sky-haze) 0%,
        var(--mist-teal) 20%,
        var(--hill-blue) 36%,
        var(--field-green) 58%,
        var(--field-deep) 100%);
  }
</style>
</head>
<body>
<main class="card-set">
  <section class="card contact-side">
    <div class="holder">
      <p class="holder-name">Daniel Hartley</p>
      <p class="holder-title">Managing Director</p>
    </div>
    <ul class="contact-list">
      <li>
        <svg viewBox="0 0 16 16" aria-hidden="true"><path fill="var(--accent-red)" d="M3 2h3l1.5 3.5-2 1.2a9 9 0 0 0 3.8 3.8l1.2-2L14 10v3a1 1 0 0 1-1 1A11 11 0 0 1 2 3a1 1 0 0 1 1-1z"/></svg>
        0412965203
      </li>
      <li>
        <svg viewBox="0 0 16 16" aria-hidden="true"><rect x="1" y="3" width="14" height="10" fill="var(--accent-red)"/><path d="M1.5 3.5 8 9l6.5-5.5" stroke="#fff" stroke-width="1.3" fill="none"/></svg>
        hello@skywardvistaphoto.com.au
      </li>
      <li>
        <svg viewBox="0 0 16 16" aria-hidden="true"><circle cx="8" cy="8" r="7" fill="var(--accent-red)"/><path d="M1 8h14M8 1c-3 3.5-3 10.5 0 14M8 1c3 3.5 3 10.5 0 14" stroke="#fff" stroke-width="1" fill="none"/></svg>
        www.skywardvistaphoto.com.au
      </li>
    </ul>
    <div class="brand-mark">
      <span class="brand-circle"></span>
      <span class="brand-name">Skyward Vista Photo</span>
    </div>
  </section>

  <section class="card photo-side">
    <div class="landscape" role="img" aria-label="Aerial photo of hazy green countryside hills and blue mountains, with a camera drone flying in the foreground at centre"></div>
  </section>
</main>
</body>
</html>
```